VANTOL GROUP

This is a company that provides executive protection. Our motto is "New Era in Protection"... I don't want this to look like other security websites. I want it to be clean and sharp and represent a new era. We are based in the bay area so maybe a picture of San Francisco in the background?
I want it to be able to funnel down a couple different categories.
1. About Us
2. Services (Executive Protection, Covert Protection, Residential Protection & Intelligence)
3. Blue Maple (Training & Consulting)
4. Contact Us
I want it to be very clean and modern. I don't want there to be any pictures of bodyguards with ear pieces like every other website.
Target Market(s)
Ultra High Net Worth Individuals
Coding
Coded - Design and coding required
Number of Pages Required
1 page
Requirements
Must have
- Colors of my Symbol
Nice to have
- City in the background, San Francisco, New York or the Pinecrest Lodge in Montana.
Should not have
- Should not look like an KVM website or have photos of bodyguards. I want this to be a clean and simple website with my logo

```html
<!DOCTYPE html>
<html lang="en">
<head>
<meta charset="utf-8">
<title>Contact Us — VANTOL GROUP</title>
<link href="https://fonts.googleapis.com/css2?family=Orbitron:wght@700;800;900&family=Mulish:wght@400;600&family=Oswald:wght@500;600&display=swap" rel="stylesheet">
<style>
  :root{
    --red:#8b181b;
    --red-deep:#560e10;
    --ink:#222222;
    --ink-soft:#555555;
    --paper:#ffffff;
    --mist:#ececec;
    --shield:#e6e6e6;
    --line:#d9d9d9;
    --foot-text:#f3e4e4;
  }
  *{box-sizing:border-box;margin:0;padding:0}
  html,body{width:836px;height:1200px;overflow:hidden;background:var(--paper)}
  body{position:relative;font-family:'Mulish',sans-serif;color:var(--ink)}
  .abs{position:absolute}

  .topbar{left:0;top:0;width:836px;height:24px;background:var(--red);color:#fff;font-size:9.5px}
  .topbar-mail{position:absolute;right:113px;top:6px;display:flex;align-items:center;gap:7px}

  .hero-art{left:0;top:24px}
  .brand{display:flex;align-items:center;gap:7px;font-family:'Orbitron',sans-serif;font-weight:800;letter-spacing:.5px}
  .brand-mark{width:16px;height:16px;background:var(--red)}
  .header-brand{left:111px;top:44px;font-size:17px;color:var(--ink)}
  .main-nav{left:364px;top:46px;display:flex;font-size:11.5px;font-weight:600;color:var(--ink)}
  .main-nav a{color:inherit;text-decoration:none;position:absolute;white-space:nowrap;top:0}
  .main-nav .active{padding-bottom:4px;border-bottom:2px solid var(--red)}
  .hero-title{left:0;width:836px;top:139px;text-align:center;font-family:'Orbitron',sans-serif;font-weight:900;font-size:27px;color:#fff;letter-spacing:1px}
  .crumbs{left:0;width:836px;top:179px;text-align:center;font-size:11.5px;color:#fff;letter-spacing:.4px}

  .kicker{left:0;width:836px;text-align:center;font-family:'Orbitron',sans-serif;font-weight:800;color:var(--red);font-size:17px;letter-spacing:.5px}
  .heading{left:0;width:836px;text-align:center;font-family:'Orbitron',sans-serif;font-weight:900;color:var(--ink);font-size:32px;letter-spacing:.5px}

  .info-card{width:130px;text-align:center}
  .info-card svg{display:block;margin:0 auto}
  .info-value{margin-top:8px;font-family:'Oswald',sans-serif;font-weight:500;font-size:15px;color:var(--ink)}

  .inquiry-art{left:0;top:600px}
  .field{background:#fff;display:flex;align-items:flex-start;box-shadow:0 1px 2px rgba(0,0,0,.08);font-size:9.5px;color:#8a8a8a}
  .field-icon{width:26px;height:100%;border-right:1px solid var(--line);display:flex;justify-content:center;padding-top:9px}
  .field-label{padding:9px 0 0 6px}
  .verify{background:#f9f9f9;border:1px solid #d3d3d3;display:flex;align-items:center;padding:0 5px;font-size:6px;color:#222}
  .verify-box{width:12px;height:12px;border:1px solid #c1c1c1;background:#fff;margin-right:5px}
  .verify-tag{margin-left:auto;font-size:4.5px;color:#777;text-align:center}
  .verify-tag span{display:block;width:9px;height:9px;margin:0 auto 2px;background:#9aa4b0;border-radius:50%}
  .submit{left:376px;top:913px;display:flex;height:26px}
  .submit-mark{width:24px;height:26px;background:var(--red)}
  .submit-label{background:#111;color:#fff;font-family:'Oswald',sans-serif;font-weight:600;font-size:12px;letter-spacing:1px;width:60px;display:flex;align-items:center;justify-content:center}

  .footer{left:0;top:992px;width:836px;height:181px;background:var(--red);color:var(--foot-text)}
  .footer-brand{position:absolute;left:111px;top:46px;font-size:18px;color:#d6d6d6}
  .footer-mail{position:absolute;left:581px;top:50px;display:flex;align-items:center;gap:6px;font-size:11px;color:#fff}
  .footer-nav{position:absolute;left:112px;top:110px;width:611px;height:31px;border-top:1px solid rgba(255,255,255,.35);border-bottom:1px solid rgba(255,255,255,.35);font-size:11px}
  .footer-nav a{position:absolute;top:9px;color:#fff;text-decoration:none}
  .footer-nav i{position:absolute;top:6px;width:1px;height:19px;background:rgba(255,255,255,.35)}
  .legal{left:0;top:1173px;width:836px;height:27px;background:var(--red-deep);color:var(--foot-text);font-size:9.5px}
  .legal span{position:absolute;top:8px}
</style>
</head>
<body>

<div class="abs topbar">
  <div class="topbar-mail">
    <svg width="10" height="8" viewBox="0 0 10 8"><rect width="10" height="8" rx="1" fill="#fff"/><path d="M0 1 L5 4.5 L10 1" stroke="#8b181b" stroke-width="1.1" fill="none"/></svg>
    info@vantolgroup.com
  </div>
</div>

<svg class="abs hero-art" width="836" height="290" viewBox="0 24 836 290">
  <defs>
    <linearGradient id="snowScene" x1="0" y1="0" x2="0" y2="1">
      <stop offset="0" stop-color="#eef1f6"/>
      <stop offset=".25" stop-color="#a9b7d3"/>
      <stop offset=".6" stop-color="#5a6fa3"/>
      <stop offset="1" stop-color="#2d3c6e"/>
    </linearGradient>
  </defs>
  <polygon points="0,206 564,311 836,196 836,206 564,311" fill="var(--red)"/>
  <polygon points="0,206 564,311 836,196" fill="var(--red)"/>
  <polygon role="img" aria-label="Snow-covered alpine valley with pine forest and cabins" points="0,24 836,24 836,196 564,295 0,206" fill="url(#snowScene)"/>
</svg>

<div class="abs brand header-brand"><span class="brand-mark"></span>VANTOL GROUP</div>
<nav class="abs main-nav">
  <a style="left:0">Home</a>
  <a style="left:64px">About Us</a>
  <a style="left:146px">Services</a>
  <a style="left:223px">Blue Maple</a>
  <a style="left:300px" class="active">Contact Us</a>
</nav>
<h1 class="abs hero-title">CONTACT US</h1>
<div class="abs crumbs">HOME &nbsp;⟶&nbsp; CONTACT US</div>

<div class="abs kicker" style="top:359px">CONTACT US</div>
<h2 class="abs heading" style="top:380px">CONTACT INFORMATION</h2>

<div class="abs info-card" style="left:249px;top:434px">
  <svg width="96" height="106" viewBox="0 0 96 106">
    <path d="M5 5 H91 V75 L48 101 L5 75 Z" fill="none" stroke="var(--shield)" stroke-width="10"/>
    <path d="M34 39 q-4 3 -1 12 q5 11 16 17 q7 3 9 -1 l2 -3 q1 -2 -1 -3 l-6 -4 q-2 -1 -3 1 l-2 2 q-6 -3 -10 -10 l2 -2 q1 -2 0 -3 l-4 -6 q-1 -2 -3 -1 z" fill="var(--ink)"/>
    <path d="M51 36 a8 8 0 0 1 8 8 M52 30 a14 14 0 0 1 13 13" stroke="var(--red)" stroke-width="2.5" fill="none" stroke-linecap="round"/>
  </svg>
  <div class="info-value">+1 555-014-2290</div>
</div>
<div class="abs info-card" style="left:457px;top:434px">
  <svg width="96" height="106" viewBox="0 0 96 106">
    <path d="M5 5 H91 V75 L48 101 L5 75 Z" fill="none" stroke="var(--shield)" stroke-width="10"/>
    <rect x="28" y="32" width="40" height="31" rx="3" fill="var(--ink)"/>
    <path d="M28 35 q0 -3 3 -3 h34 q3 0 3 3 v3 L48 50 L28 38 z" fill="var(--red)"/>
  </svg>
  <div class="info-value">info@vantolgroup.com</div>
</div>

<svg class="abs inquiry-art" width="836" height="392" viewBox="0 600 836 392">
  <polygon points="0,729 269,615 836,713 836,992 0,992" fill="var(--red)"/>
  <polygon points="0,729 269,632 836,718 836,992 0,992" fill="var(--mist)"/>
</svg>

<div class="abs kicker" style="top:703px">CONTACT FORM</div>
<h2 class="abs heading" style="top:725px">QUICK INQUIRY</h2>

<div class="abs field" style="left:157px;top:783px;width:255px;height:29px">
  <div class="field-icon"><svg width="9" height="10" viewBox="0 0 9 10"><circle cx="4.5" cy="3" r="2.3" fill="none" stroke="var(--red)"/><rect x="1" y="6" width="7" height="3.5" rx="1" fill="none" stroke="var(--red)"/></svg></div>
  <div class="field-label">Full Name*</div>
</div>
<div class="abs field" style="left:423px;top:783px;width:256px;height:29px">
  <div class="field-icon"><svg width="10" height="8" viewBox="0 0 10 8"><rect x=".5" y=".5" width="9" height="7" fill="none" stroke="var(--red)"/><path d="M.5 1 L5 4.5 L9.5 1" fill="none" stroke="var(--red)"/></svg></div>
  <div class="field-label">Email Address*</div>
</div>
<div class="abs field" style="left:157px;top:822px;width:255px;height:70px">
  <div class="field-icon"><svg width="10" height="9" viewBox="0 0 10 9"><ellipse cx="5" cy="4" rx="4.5" ry="3.3" fill="none" stroke="var(--red)"/><path d="M2 6.5 L1 8.5 L4 7.2" fill="none" stroke="var(--red)"/></svg></div>
  <div class="field-label">Message</div>
</div>
<div class="abs field" style="left:423px;top:822px;width:256px;height:29px">
  <div class="field-icon"><svg width="9" height="9" viewBox="0 0 9 9"><path d="M1.5 1 q-1.5 1 0 4 q2 3 5 3.5 q1 0 1.5 -1 l-2 -1.5 l-1 1 q-2 -1 -3 -3 l1 -1 z" fill="none" stroke="var(--red)" stroke-width=".9"/></svg></div>
  <div class="field-label">Phone Number*</div>
</div>
<div class="abs verify" style="left:423px;top:862px;width:256px;height:30px">
  <div class="verify-box"></div>I'm not a robot
  <div class="verify-tag"><span></span>Verify</div>
</div>

<div class="abs submit"><div class="submit-mark"></div><div class="submit-label">SUBMIT</div></div>

<footer class="abs footer">
  <div class="brand footer-brand"><span class="brand-mark" style="background:#d6d6d6"></span>VANTOL GROUP</div>
  <div class="footer-mail">
    <svg width="24" height="26" viewBox="0 0 24 26"><path d="M0 0 H24 V19 L12 26 L0 19 Z" fill="var(--red-deep)"/><rect x="6" y="8" width="12" height="9" rx="1" fill="#fff"/><path d="M6 9 L12 13 L18 9" fill="none" stroke="var(--red-deep)" stroke-width="1.2"/></svg>
    info@vantolgroup.com
  </div>
  <nav class="footer-nav">
    <a style="left:31px">Home</a><i style="left:96px"></i>
    <a style="left:144px">About Us</a><i style="left:234px"></i>
    <a style="left:278px">Services</a><i style="left:368px"></i>
    <a style="left:405px">Blue Maple</a><i style="left:496px"></i>
    <a style="left:526px">Contact Us</a>
  </nav>
</footer>
<div class="abs legal">
  <span style="left:113px">Copyright © 2021 Vantol Group. All Rights Reserved.</span>
  <span style="right:113px">Privacy Policy</span>
</div>

</body>
</html>
```